Onboarding Infographic/brochure

We are a small criminal defense firm looking to create some sort of infographic or brochure that we can onboard new clients with. We are currently sending it out via email but want something a bit cooler and fun to send to clients. The information is:

A Few Quick Rules

We are here to help each step of the way. While questions are never discouraged, this letter will answer some of the most common ones we get asked.

Communications

As a client, you should always be in the loop. While we will try to respond to questions as quickly as possible, sometimes we are unable to respond right away. Do not worry - we promise to get back to you soon. Some questions might take some time to research, and a correct answer is better than a quick one.

Appointments

One of the benefits of having an attorney is the ability to discuss your case outside of court, minus the stress and headaches. If you need an appointment, please contact the office.

Appointments must be scheduled in advance. We do not want you to make a special trip to the office only to learn that we are in court or otherwise unavailable.

Jail Visits

If your family member is currently in jail, we take that very seriously. We will visit your loved one and introduce ourselves. While the case is ongoing, we ask that a family member be designated a “contact” person so that messages can be relayed quickly. Never discuss the facts of the case over the phone with someone who is in jail. Jail calls are recorded and we have seen too many cases go south based on remarks made over recorded lines.

Police Reports and Discovery

We will do our best to provide you with copies of everything we receive on your case. Most information will be emailed, so please keep your email address up to date.

Changes in Contact Information

If you move or change numbers during the case, please let us know. It is difficult to help if we are unable to reach you, and helping you is why we are here.

Court Appearances

Cases do not get resolved as quickly as they do on television. Expect there to be several hearings in your case and it may be necessary for you to attend one or more of them. If a hearing is set, you will receive notice of the date and time of each hearing.

Billing and Collections

We understand that this investment was a huge decision for you. As we focus on providing the best representation, we will need for you to stay on schedule with any payment arrangements agreed to at the time of your initial consultation.

Again, thank you for your trust in us. We look forward to getting a fantastic outcome on your case.

Target Market(s)

Criminal defense clients and their families

Industry/Entity Type

Legal

Font styles to use
Serif

Requirements
Must have
• Must incorporate all of the rules we email out. Would like diagrams, images or pictures
Nice to have
• We attached a Welcome brochure. Not sure I want it to look super similar, hence the request for infographic.

```html
<!DOCTYPE html>
<html lang="en">
<head>
<meta charset="utf-8">
<title>Veritas Defense Group – Client Onboarding</title>
<link rel="stylesheet" href="https://fonts.googleapis.com/css2?family=Montserrat:wght@700;800&family=Arimo:wght@400;700&family=Oswald:wght@500&display=swap">
<style>
:root{
  --backdrop:#6b6b6d;
  --blue:#0a4db5;
  --blue-deep:#1d2f8c;
  --sky:#0e96dc;
  --lime:#d4df22;
  --lime-head:#dfe820;
  --orange:#f5981c;
  --ink:#111111;
  --grey-text:#6d6e71;
  --white:#ffffff;
}
*{margin:0;padding:0;box-sizing:border-box}
html,body{width:1200px;height:1200px;overflow:hidden;background:var(--backdrop)}
.flyer{position:absolute;left:224px;top:67px;width:752px;height:1064px;overflow:hidden;background:var(--white)}
.sheet{position:absolute;left:0;top:0;width:1212px;height:1714px;transform:scale(0.6205);transform-origin:0 0;font-family:"Arimo",Arial,sans-serif}
.art{position:absolute;inset:0;width:1212px;height:1714px}
.brand-name{position:absolute;left:64px;top:222px;font-family:"Montserrat",Arial,sans-serif;font-weight:700;font-size:78px;line-height:70px;color:var(--ink);letter-spacing:-1px}
.heading{position:absolute;font-family:"Montserrat",Arial,sans-serif;font-weight:800;font-size:35px;line-height:36px;white-space:nowrap}
.body{position:absolute;font-size:20.5px;line-height:24px}
.body.just{text-align:justify}
.line{position:absolute;font-size:20.5px;line-height:24px;white-space:nowrap;text-align:justify;text-align-last:justify}
.line.end{text-align-last:left}
.rules-title{left:675px;top:60px;color:var(--lime-head)}
.rules-text{left:675px;top:110px;width:428px;color:var(--white);text-align:justify}
.comm-title{right:639px;top:518px;color:var(--white);font-size:30px}
.comm-line{color:var(--white)}
.appt-title{left:645px;top:558px;color:var(--lime-head)}
.appt-line{color:var(--white)}
.jail-title{left:128px;top:888px;color:var(--lime-head);font-size:33px}
.jail-line{color:var(--white)}
.police-title{left:795px;top:878px;color:var(--ink);font-size:29px;line-height:31px}
.police-line{color:var(--ink)}
.court-title{left:639px;top:1165px;color:var(--orange)}
.court-text{left:639px;top:1218px;width:511px;color:var(--orange)}
.change-title{left:45px;top:1358px;color:var(--blue);line-height:37px}
.change-text{left:46px;top:1442px;width:440px;color:var(--blue)}
.billing-title{left:638px;top:1393px;color:var(--grey-text)}
.billing-text{left:702px;top:1442px;width:448px;color:var(--grey-text)}
.hotline{position:absolute;left:433px;top:760px;width:350px;text-align:center;font-family:"Oswald",Arial,sans-serif;font-weight:500}
.hotline .label{display:block;color:var(--orange);font-size:24px;line-height:26px}
.hotline .number{display:block;color:var(--blue);font-size:38px;line-height:42px;margin-bottom:0}
.contact-list{position:absolute;left:60px;top:1596px;font-family:"Arimo",Arial,sans-serif;font-weight:700;font-size:28px;line-height:40px;color:var(--ink);list-style:none}
.contact-list li{display:flex;align-items:center;gap:18px}
.contact-list svg{width:32px;height:32px}
</style>
</head>
<body>
<main class="flyer">
  <div class="sheet">
    <svg class="art" viewBox="0 0 1212 1714" aria-hidden="false">
      <defs>
        <linearGradient id="courthouseTone" x1="0" y1="0" x2="1" y2="1">
          <stop offset="0" stop-color="#ffffff"/>
          <stop offset="0.5" stop-color="#e6ebf1"/>
          <stop offset="1" stop-color="#f4f6f9"/>
        </linearGradient>
        <linearGradient id="orangeFade" x1="0" y1="0" x2="1" y2="0">
          <stop offset="0.55" stop-color="#f5981c"/>
          <stop offset="1" stop-color="#8a4a0c"/>
        </linearGradient>
        <linearGradient id="handshakeTone" x1="0" y1="0" x2="1" y2="1">
          <stop offset="0" stop-color="#0a4db5" stop-opacity="0"/>
          <stop offset="0.45" stop-color="#3f6cb8"/>
          <stop offset="0.75" stop-color="#b08a78"/>
          <stop offset="1" stop-color="#254c9a"/>
        </linearGradient>
        <linearGradient id="signingTone" x1="0" y1="0" x2="0" y2="1">
          <stop offset="0" stop-color="#cfd2d6"/>
          <stop offset="0.35" stop-color="#7d8187"/>
          <stop offset="0.6" stop-color="#2a2b2e"/>
          <stop offset="1" stop-color="#151515"/>
        </linearGradient>
        <linearGradient id="jailBlue" x1="0" y1="0" x2="1" y2="1">
          <stop offset="0" stop-color="#0a47b0"/>
          <stop offset="1" stop-color="#1d2f8c"/>
        </linearGradient>
        <radialGradient id="discFill" cx="0.4" cy="0.3" r="0.8">
          <stop offset="0" stop-color="#ffffff"/>
          <stop offset="1" stop-color="#d2d3d5"/>
        </radialGradient>
        <filter id="softShadow" x="-20%" y="-20%" width="140%" height="140%">
          <feDropShadow dx="0" dy="3" stdDeviation="5" flood-color="#000" flood-opacity="0.3"/>
        </filter>
      </defs>

      <!-- top left photo zone -->
      <rect x="120" y="0" width="488" height="560" fill="url(#courthouseTone)" role="img" aria-label="Faded photo of courthouse columns"/>
      <path d="M0,562 Q120,680 145,855 L0,855 Z" fill="var(--sky)"/>
      <path d="M145,855 A463,463 0 0 1 608,392 L608,855 Z" fill="url(#orangeFade)"/>

      <!-- top right panel -->
      <rect x="608" y="0" width="604" height="855" fill="var(--blue)"/>
      <rect x="608" y="190" width="604" height="430" fill="url(#handshakeTone)" role="img" aria-label="Photo of a business handshake"/>
      <path d="M1212,57 Q1150,130 1126,157 Q1170,200 1212,262 Z" fill="var(--lime)"/>
      <path d="M608,300 C800,300 960,380 1010,450 C1090,560 1140,700 1145,855 L608,855 Z" fill="url(#signingTone)" role="img" aria-label="Photo of a hand signing documents with a pen"/>
      <path d="M608,300 C800,300 960,380 1010,450 C1090,560 1140,700 1145,855" fill="none" stroke="var(--white)" stroke-width="10"/>

      <!-- lower left -->
      <rect x="0" y="855" width="608" height="859" fill="var(--lime)"/>
      <path d="M70,855 A538,538 0 0 0 608,1393" fill="none" stroke="var(--white)" stroke-width="18"/>
      <path d="M91,855 A517,517 0 0 0 608,1372 L608,855 Z" fill="url(#jailBlue)"/>
      <path d="M0,1582 Q30,1610 48,1637 Q30,1664 0,1692 Z" fill="var(--ink)"/>

      <!-- lower right -->
      <path d="M608,855 L1070,855 C1070,960 1030,1060 980,1135 L608,1135 Z" fill="var(--lime)"/>

      <!-- hotline disc -->
      <circle cx="608" cy="855" r="176" fill="var(--white)" filter="url(#softShadow)"/>
      <circle cx="608" cy="855" r="160" fill="url(#discFill)"/>
      <path d="M596,722 c-6,4 -8,10 -4,17 c6,11 15,21 27,28 c7,4 13,2 17,-4 l-8,-8 c-3,-2 -6,-2 -8,1 c-7,-4 -13,-10 -17,-17 c3,-2 3,-5 1,-8 Z" fill="none" stroke="var(--orange)" stroke-width="3" stroke-linejoin="round"/>

      <!-- icon: communications -->
      <g transform="translate(483,417)">
        <circle r="62" fill="var(--white)" filter="url(#softShadow)"/>
        <circle r="52" fill="url(#discFill)"/>
        <rect x="-20" y="-42" width="40" height="20" rx="6" fill="var(--sky)"/>
        <path d="M-4,-22 l4,6 l4,-6 Z" fill="var(--sky)"/>
        <rect x="-38" y="-8" width="32" height="24" rx="8" fill="#555"/>
        <path d="M-30,16 l-4,10 l12,-10 Z" fill="#555"/>
        <rect x="6" y="-8" width="32" height="24" rx="8" fill="#555"/>
        <path d="M30,16 l4,10 l-12,-10 Z" fill="#555"/>
      </g>

      <!-- icon: calendar -->
      <g transform="translate(1023,509)">
        <circle r="62" fill="var(--white)" filter="url(#softShadow)"/>
        <circle r="52" fill="url(#discFill)"/>
        <rect x="-30" y="-26" width="58" height="54" rx="5" fill="none" stroke="#666" stroke-width="4"/>
        <line x1="-30" y1="-14" x2="28" y2="-14" stroke="#666" stroke-width="4"/>
        <g fill="#666">
          <rect x="-22" y="-34" width="4" height="12"/><rect x="-10" y="-34" width="4" height="12"/>
          <rect x="2" y="-34" width="4" height="12"/><rect x="14" y="-34" width="4" height="12"/>
          <rect x="-22" y="-6" width="7" height="7"/><rect x="-11" y="-6" width="7" height="7"/><rect x="0" y="-6" width="7" height="7"/>
          <rect x="-22" y="6" width="7" height="7"/><rect x="-11" y="6" width="7" height="7"/>
        </g>
        <path d="M2,10 l9,9 l20,-24" fill="none" stroke="var(--sky)" stroke-width="6" stroke-linecap="round" stroke-linejoin="round"/>
      </g>

      <!-- icon: jail -->
      <g transform="translate(92,1137)">
        <circle r="62" fill="var(--white)" filter="url(#softShadow)"/>
        <circle r="52" fill="url(#discFill)"/>
        <g fill="#666">
          <rect x="-32" y="-32" width="64" height="5"/>
          <rect x="-32" y="27" width="64" height="5"/>
          <rect x="-28" y="-27" width="5" height="54"/>
          <rect x="-16" y="-27" width="5" height="54"/>
          <rect x="-4" y="-27" width="5" height="54"/>
          <rect x="8" y="-27" width="5" height="54"/>
          <rect x="20" y="-27" width="5" height="54"/>
        </g>
        <circle cx="-1" cy="-2" r="6" fill="#666"/>
      </g>

      <!-- icon: police reports -->
      <g transform="translate(1100,982)">
        <circle r="62" fill="var(--white)" filter="url(#softShadow)"/>
        <circle r="52" fill="url(#discFill)"/>
        <circle cx="-8" cy="-8" r="20" fill="var(--white)" stroke="#666" stroke-width="6"/>
        <circle cx="-8" cy="-8" r="10" fill="var(--sky)"/>
        <line x1="7" y1="7" x2="24" y2="24" stroke="#666" stroke-width="9" stroke-linecap="round"/>
      </g>

      <!-- icon: billing -->
      <g transform="translate(618,1535)">
        <circle r="62" fill="var(--white)" filter="url(#softShadow)"/>
        <circle r="52" fill="url(#discFill)"/>
        <rect x="-18" y="-32" width="42" height="58" rx="3" fill="var(--white)" stroke="#666" stroke-width="4"/>
        <path d="M-30,10 v18 a6,6 0 0 0 6,6 h38" fill="none" stroke="#666" stroke-width="4"/>
        <text x="3" y="-3" text-anchor="middle" font-family="Arimo, Arial, sans-serif" font-weight="700" font-size="26" fill="var(--sky)">$</text>
        <line x1="-8" y1="8" x2="14" y2="8" stroke="#666" stroke-width="3"/>
        <line x1="-8" y1="15" x2="14" y2="15" stroke="#666" stroke-width="3"/>
      </g>
    </svg>

    <h1 class="brand-name">VERITAS<br>DEFENSE<br>GROUP</h1>

    <h2 class="heading rules-title">A FEW QUICK RULES</h2>
    <p class="body rules-text">We are here to help each step of the way. While questions are never discouraged, this letter will answer some of the most common ones we get asked.</p>

    <h2 class="heading comm-title">COMMUNICATIONS</h2>
    <div class="comm-line line" style="left:290px;width:281px;top:565px">As a client, you should always</div>
    <div class="comm-line line" style="left:268px;width:303px;top:589px">be in the loop. While we will try to</div>
    <div class="comm-line line" style="left:250px;width:321px;top:613px">respond to questions as quickly as</div>
    <div class="comm-line line" style="left:234px;width:337px;top:637px">possible, sometimes we are unable</div>
    <div class="comm-line line" style="left:220px;width:351px;top:661px">to respond right away. Do not worry -</div>
    <div class="comm-line line" style="left:208px;width:300px;top:685px">we promise to get back to you</div>
    <div class="comm-line line" style="left:198px;width:280px;top:709px">soon. Some questions might</div>
    <div class="comm-line line" style="left:190px;width:266px;top:733px">take some time to research,</div>
    <div class="comm-line line" style="left:183px;width:259px;top:757px">and a correct answer is</div>
    <div class="comm-line line end" style="left:178px;top:781px">better than a quick one.</div>

    <h2 class="heading appt-title">APPOINTMENTS</h2>
    <div class="appt-line line" style="left:647px;width:403px;top:604px">One of the benefits of having an attorney is</div>
    <div class="appt-line line" style="left:647px;width:416px;top:628px">the ability to discuss your case outside of</div>
    <div class="appt-line line" style="left:647px;width:428px;top:652px">court, minus the stress and headaches. If you</div>
    <div class="appt-line line" style="left:697px;width:388px;top:676px">need an appointment, please contact the</div>
    <div class="appt-line line" style="left:733px;width:362px;top:700px">office. Appointments must be</div>
    <div class="appt-line line" style="left:756px;width:346px;top:724px">scheduled in advance. We do not</div>
    <div class="appt-line line" style="left:772px;width:336px;top:748px">want you to make a special trip to</div>
    <div class="appt-line line" style="left:784px;width:328px;top:772px">the office only to learn that we are in</div>
    <div class="appt-line line end" style="left:790px;top:796px">court or otherwise unavailable.</div>

    <div class="hotline">
      <span class="label">TOLL FREE</span>
      <span class="number">(888) 555-0142</span>
      <span class="label">LA AREA</span>
      <span class="number">(213) 555-0178</span>
      <span class="label">INLAND</span>
      <span class="number">(909) 555-0193</span>
    </div>

    <h2 class="heading jail-title">JAIL VISITS</h2>
    <div class="jail-line line" style="left:133px;width:285px;top:935px">If your family member is</div>
    <div class="jail-line line" style="left:138px;width:292px;top:959px">currently in jail, we take that</div>
    <div class="jail-line line" style="left:146px;width:299px;top:983px">very seriously. We will visit your</div>
    <div class="jail-line line" style="left:153px;width:315px;top:1007px">loved one and introduce</div>
    <div class="jail-line line" style="left:163px;width:335px;top:1031px">ourselves. While the case is</div>
    <div class="jail-line line" style="left:175px;width:375px;top:1055px">ongoing, we ask that a family member</div>
    <div class="jail-line line" style="left:188px;width:389px;top:1079px">be designated a “contact” person so that</div>
    <div class="jail-line line" style="left:203px;width:374px;top:1103px">messages can be relayed quickly. Never</div>
    <div class="jail-line line" style="left:220px;width:357px;top:1127px">discuss the facts of the case over the</div>
    <div class="jail-line line" style="left:239px;width:338px;top:1151px">phone with someone who is in jail.</div>
    <div class="jail-line line" style="left:261px;width:316px;top:1175px">Jail calls are recorded and we</div>
    <div class="jail-line line" style="left:287px;width:290px;top:1199px">have seen too many cases go</div>
    <div class="jail-line line" style="left:316px;width:261px;top:1223px">south based on remarks</div>
    <div class="jail-line line" style="left:352px;width:225px;top:1247px">made over recorded</div>
    <div class="jail-line line end" style="left:395px;top:1271px">lines.</div>

    <h2 class="heading police-title">POLICE REPORTS<br>&amp; DISCOVERY</h2>
    <div class="police-line line" style="left:758px;width:265px;top:958px">We will do our best to</div>
    <div class="police-line line" style="left:739px;width:276px;top:982px">provide you with copies of</div>
    <div class="police-line line" style="left:711px;width:294px;top:1006px">everything we receive on your</div>
    <div class="police-line line" style="left:662px;width:332px;top:1030px">case. Most information will be</div>
    <div class="police-line line end" style="left:639px;top:1054px">emailed, so please keep your email</div>
    <div class="police-line line end" style="left:639px;top:1078px">address up to date.</div>

    <h2 class="heading court-title">COURT APPEARANCES</h2>
    <p class="body just court-text">Cases do not get resolved as quickly as they do on television. Expect there to be several hearings in your case and it may be necessary for you to attend one or more of them. If a hearing is set, you will receive notice of the date and time of each hearing.</p>

    <h2 class="heading change-title">CHANGES IN<br>CONTACT INFORMATION</h2>
    <p class="body just change-text">If you move or change numbers during the case, please let us know. It is difficult to help if we are unable to reach you, and helping you is why we are here.</p>

    <h2 class="heading billing-title">BILLING &amp; COLLECTIONS</h2>
    <p class="body just billing-text">We understand that this investment was a huge decision for you. As we focus on providing the best representation, we will need for you to stay on schedule with any payment arrangements agreed to at the time of your initial consultation. Again, thank you for your trust in us. We look forward to getting a fantastic outcome on your case.</p>

    <ul class="contact-list">
      <li>
        <svg viewBox="0 0 32 32" aria-hidden="true"><rect x="2" y="7" width="28" height="19" fill="none" stroke="#111" stroke-width="2"/><path d="M2,7 L16,18 L30,7 M2,26 L12,16 M30,26 L20,16" fill="none" stroke="#111" stroke-width="2"/></svg>
        <span>info@veritasdefensegroup.com</span>
      </li>
      <li>
        <svg viewBox="0 0 32 32" aria-hidden="true"><circle cx="16" cy="16" r="13" fill="none" stroke="#111" stroke-width="2"/><ellipse cx="16" cy="16" rx="6" ry="13" fill="none" stroke="#111" stroke-width="2"/><path d="M3,16 H29 M5,9 H27 M5,23 H27" stroke="#111" stroke-width="2"/></svg>
        <span>www.veritasdefensegroup.com</span>
      </li>
    </ul>
  </div>
</main>
</body>
</html>
```